Web Developer Needs a Business Card Design

I need a personal business card design that represents me as a web developer for potential employers. I would like the background to be a dark color on the front for contrast with my logo and name. The back will have all my information along with a smaller version of the logo. I want something with a modern look and feel, not too conservative. This will be used for potential employers and freelance work.

Industry/Entity Type

Business

Contact Information for Business Card

Front should have my logo and name. The back should have all my personal information which would include: name: Tom Varulek, phone: 570-614-3098, email: tomvarulek@quillbox.net, website url: www.tomvarulek.net, logo, web developer.

Font styles to use
Sans Serif

Requirements
Must have
• Must include my logo. The color palette base color will be the logo color.

```html
<!DOCTYPE html>
<html lang="en">
<head>
<meta charset="utf-8">
<title>Tom Varulek — Business Card</title>
<link rel="stylesheet" href="https://fonts.googleapis.com/css2?family=Open+Sans:wght@400;600;700&display=swap">
<style>
  :root {
    --teal-deep: #6cc8b5;
    --teal-bright: #52e3c4;
    --teal-text: #3cc9a8;
    --ink: #2b2b2b;
    --paper: #ffffff;
    --backdrop: #eef1f0;
  }
  * { box-sizing: border-box; margin: 0; padding: 0; }
  html, body {
    width: 1200px; height: 900px; overflow: hidden;
    background: var(--backdrop);
    font-family: "Open Sans", Arial, sans-serif;
  }
  .stage {
    position: relative; width: 1200px; height: 900px;
    display: flex; flex-direction: column; align-items: center; justify-content: center; gap: 50px;
  }
  .card {
    position: relative; width: 560px; height: 320px; overflow: hidden;
    box-shadow: 0 6px 18px rgba(0,0,0,0.15);
  }
  /* Front */
  .card-front {
    background: var(--teal-deep); color: var(--paper);
    display: flex; flex-direction: column; align-items: center; justify-content: center;
  }
  .front-mark {
    width: 120px; height: 120px; border-radius: 50%;
    border: 4px solid rgba(255,255,255,0.55);
    display: flex; align-items: center; justify-content: center;
    font-weight: 700; font-size: 40px; color: rgba(255,255,255,0.75);
    margin-bottom: 18px;
  }
  .front-name { font-weight: 700; font-size: 40px; line-height: 1.1; }
  .front-title { font-weight: 400; font-size: 20px; margin-top: 4px; }
  /* Back */
  .card-back { background: var(--paper); }
  .back-details { position: absolute; left: 330px; top: 28px; }
  .back-name { color: var(--teal-text); font-weight: 700; font-size: 19px; line-height: 1.1; }
  .back-title { color: var(--ink); font-size: 13px; margin-bottom: 16px; }
  .contact-list { list-style: none; padding-left: 34px; }
  .contact-list li {
    display: flex; align-items: center; gap: 6px;
    color: var(--ink); font-size: 13.5px; line-height: 1.6;
  }
  .contact-list svg { width: 12px; height: 12px; flex: none; fill: var(--teal-deep); }
  .back-band {
    position: absolute; left: 0; right: 0; top: 192px; height: 72px;
    background: var(--teal-bright);
  }
  .back-mark {
    position: absolute; left: 108px; top: 163px;
    width: 130px; height: 130px; border-radius: 50%;
    background: var(--paper);
    display: flex; align-items: center; justify-content: center;
  }
  .back-mark span {
    width: 110px; height: 110px; border-radius: 50%;
    background: var(--teal-deep); color: var(--paper);
    display: flex; align-items: center; justify-content: center;
    font-weight: 700; font-size: 36px;
  }
</style>
</head>
<body>
<main class="stage">
  <section class="card card-front">
    <div class="front-mark">TV</div>
    <h1 class="front-name">Tom Varulek</h1>
    <p class="front-title">Front-End Developer</p>
  </section>

  <section class="card card-back">
    <div class="back-details">
      <h2 class="back-name">Tom Varulek</h2>
      <p class="back-title">Front-End Developer</p>
      <ul class="contact-list">
        <li><svg viewBox="0 0 24 24"><path d="M6.6 10.8a15.1 15.1 0 0 0 6.6 6.6l2.2-2.2a1 1 0 0 1 1-.25 11.4 11.4 0 0 0 3.6.57 1 1 0 0 1 1 1V20a1 1 0 0 1-1 1A17 17 0 0 1 3 4a1 1 0 0 1 1-1h3.5a1 1 0 0 1 1 1c0 1.25.2 2.45.57 3.57a1 1 0 0 1-.25 1z"/></svg>570-614-3098</li>
        <li><svg viewBox="0 0 24 24"><path d="M2 5h20v14H2z M2 5l10 8 10-8" /></svg>tomvarulek@quillbox.net</li>
        <li><svg viewBox="0 0 24 24"><path d="M10 14a4 4 0 0 1 0-5.6l3-3a4 4 0 0 1 5.6 5.6l-1.5 1.5-1.4-1.4 1.5-1.5a2 2 0 0 0-2.8-2.8l-3 3a2 2 0 0 0 0 2.8zm4-4a4 4 0 0 1 0 5.6l-3 3a4 4 0 0 1-5.6-5.6l1.5-1.5 1.4 1.4-1.5 1.5a2 2 0 0 0 2.8 2.8l3-3a2 2 0 0 0 0-2.8z"/></svg>www.tomvarulek.net</li>
      </ul>
    </div>
    <div class="back-band"></div>
    <div class="back-mark"><span>TV</span></div>
  </section>
</main>
</body>
</html>
```